Website Comps for Famous Southern BBQ Restaurant in Alabama

We need an authentic, brand-focused redesign for a restaurant.

We need an authentic look.
The client really likes this website.
https://pelmarsmokehouse.example/

I don't want to see a bunch of crazy colors.
Avoid image sliders on the homepage. I hate those.

Please mockup the following three pages:
Homepage
Interior page (for mockup purposes, you can do an About page)
Menu page

I only need the PSD's; not the website coded.

Here is the current website: www.kortiespit.example

https://pelmarsmokehouse.example/

Here are some additional stock photos. New photos will be shot, but these may help for your mock-up designs.
https://files.quillbox.example/sh/83kkqvtrd41zpa7/XQM20PbT9LyRk-wnEuvJ3tpd?dl=0
Updates

I realize we don't have a lot of high-quality photos to work with.Those will be shot.Here are some additional stock photos that may help.https://files.quillbox.example/sh/83kkqvtrd41zpa7/XQM20PbT9LyRk-wnEuvJ3tpd?dl=0 Added Saturday, June 10, 2017

Target Market(s)

United states

Industry/Entity Type

Restaurant

Number of Pages Required

3 page

Font styles to use
Sans Serif

Colors

Designer to choose colors to be used in the design.

Requirements
Must have
• An authentic look.
• The client really likes this website.
• https://pelmarsmokehouse.example/
• It's simple, bold, and vintage at the same time.
• That is what we want.
• Our existing website is
• kortiespit.example
Nice to have
• Simplicity. Something that makes the food look good.
• Possibly a background.
• Logo:
• https://files.quillbox.example/s/t62bnezwhk0qpl3/kories-pit-lakeview.png?dl=0
• Here is a sampling of photos for your comps:
• https://files.quillbox.example/sh/59ryhdupqv2ncmx/MPT4c1ZLvWeQjHoNUyrA8BfxKs?dl=0
Should not have
• Nothing too busy.
• Not too many colors.
• Keep it simple, authentic, "down home."
• No homepage image sliders.

```html
<!DOCTYPE html>
<html lang="en">
<head>
<meta charset="utf-8">
<title>Smokehouse Homepage – Gallery, Offer and Blog</title>
<link rel="stylesheet" href="https://fonts.googleapis.com/css2?family=Oswald:wght@500;700&family=Lato:wght@300;400;700&display=swap">
<style>
:root{
  --orange:#f5a11e;
  --brown:#4a1a08;
  --ink:#333333;
  --muted:#666666;
  --white:#ffffff;
  --dark:#120d09;
  --card-border:#e4e4e4;
}
*{box-sizing:border-box;margin:0;padding:0}
html,body{width:1200px;height:1200px;overflow:hidden;background:var(--white)}
body{position:relative;font-family:'Lato',sans-serif;color:var(--ink)}
.abs{position:absolute}

.strip-photo{top:0;height:33px}
.strip-photo.one{left:147px;width:224px;background:linear-gradient(180deg,#6b5a4a,#8a9aa0)}
.strip-photo.two{left:377px;width:224px;background:linear-gradient(90deg,#2a2a2a,#6e6e6e,#2a2a2a)}
.strip-photo.three{left:606px;width:447px;background:linear-gradient(90deg,#3a1808,#7a3a18,#2d140a)}

.section-title{left:0;width:1200px;text-align:center;font-family:'Oswald',sans-serif;font-weight:700;color:var(--orange);text-transform:uppercase;letter-spacing:.5px;line-height:1}
.section-sub{left:0;width:1200px;text-align:center;line-height:1}
.flourish{left:528px;width:146px;height:16px;border-radius:8px}
.flourish.on-light{background:linear-gradient(90deg,transparent,#555 20%,#222 50%,#555 80%,transparent)}
.flourish.on-dark{background:linear-gradient(90deg,transparent,#ccc 20%,#fff 50%,#ccc 80%,transparent)}

.gallery-title{top:89px;font-size:39px}
.gallery-sub{top:138px;font-size:15.5px;color:var(--ink)}
.gallery-flourish{top:167px;opacity:.75}

.chef-card{top:231px;width:202px;height:207px;border:1px solid var(--card-border);box-shadow:0 0 4px rgba(0,0,0,.12);background:var(--white)}
.chef-photo{position:absolute;left:7px;top:7px;width:187px;height:191px}
.chef-info{top:464px;width:202px;text-align:center}
.chef-name{font-family:'Oswald',sans-serif;font-weight:700;font-size:16px;color:var(--brown);line-height:20px}
.chef-role{font-size:14px;color:var(--orange);margin-top:6px;line-height:18px}
.chef-bio{font-size:11.5px;color:var(--muted);margin-top:5px;line-height:15px}

.offer{left:0;top:578px;width:1200px;height:484px;background:radial-gradient(ellipse at 62% 70%,#5a3214 0%,#2a1609 35%,var(--dark) 75%)}
.offer-title{top:642px;font-size:40px}
.offer-sub{top:686px;font-size:15px;color:var(--white)}
.offer-flourish{top:715px}
.form-heading{left:147px;top:757px;font-size:19.5px;font-weight:700;color:var(--white);letter-spacing:.2px}
.field{height:36px;width:446px;border:1px solid #e8e8e8;border-radius:2px;background:rgba(0,0,0,.25);color:#cfcfcf;font-size:10.5px;font-weight:400;padding-left:16px;display:flex;align-items:center}
.field svg{position:absolute;right:14px;top:10px}
.field.left{left:147px}.field.right{left:608px}
.row1{top:797px}.row2{top:850px}.row3{top:902px}
.select-btn{position:absolute;right:0;top:0;width:16px;height:34px;background:#8d8d8d;display:flex;align-items:center;justify-content:center}
.offer-note{left:147px;top:965px;font-size:13.5px;color:var(--white)}
.reserve-btn{left:908px;top:952px;width:145px;height:46px;background:var(--orange);color:#1a1a1a;font-size:10px;font-weight:700;display:flex;align-items:center;justify-content:center;letter-spacing:.2px}

.blog-title{top:1118px;font-size:39px}
.blog-sub{top:1167px;font-size:15.5px;color:var(--ink)}
.blog-flourish{top:1194px;opacity:.75}
</style>
</head>
<body>

<div class="abs strip-photo one" role="img" aria-label="Photo of smoked brisket on a board"></div>
<div class="abs strip-photo two" role="img" aria-label="Photo of a pitmaster in a restaurant t-shirt"></div>
<div class="abs strip-photo three" role="img" aria-label="Photo of barbecue ribs with slaw"></div>

<h2 class="abs section-title gallery-title">Food Gallery</h2>
<p class="abs section-sub gallery-sub">Lisis Pretium Nunc Elementum Ligula Lobortis Eget</p>
<div class="abs flourish on-light gallery-flourish" role="img" aria-label="Decorative scroll flourish"></div>

<div class="abs chef-card" style="left:154px"><div class="chef-photo" role="img" aria-label="Photo of a senior chef giving an OK sign" style="background:linear-gradient(160deg,#6a5a50,#d8d4d0 55%,#f2f2f2)"></div></div>
<div class="abs chef-card" style="left:385px"><div class="chef-photo" role="img" aria-label="Photo of a chef holding a plated salad" style="background:linear-gradient(160deg,#8a8a8a,#e8e6e4 50%,#9a8a50)"></div></div>
<div class="abs chef-card" style="left:614px"><div class="chef-photo" role="img" aria-label="Photo of a smiling chef leaning over a plate" style="background:linear-gradient(160deg,#7a6a5a,#e6e2de 55%,#f4f4f4)"></div></div>
<div class="abs chef-card" style="left:845px"><div class="chef-photo" role="img" aria-label="Photo of a chef garnishing plated dishes" style="background:linear-gradient(160deg,#3a3a3a,#dcdcdc 50%,#8a5a30)"></div></div>

<div class="abs chef-info" style="left:154px"><h3 class="chef-name">FUSCE SUSCIPIT</h3><p class="chef-role">Malesuada Quisque</p><p class="chef-bio">Ementum ligula lobortis ege quisque<br>interdum nec tellus</p></div>
<div class="abs chef-info" style="left:385px"><h3 class="chef-name">FUSCE SUSCIPIT</h3><p class="chef-role">Malesuada Quisque</p><p class="chef-bio">Ementum ligula lobortis ege quisque<br>interdum nec tellus</p></div>
<div class="abs chef-info" style="left:614px"><h3 class="chef-name">FUSCE SUSCIPIT</h3><p class="chef-role">Malesuada Quisque</p><p class="chef-bio">Ementum ligula lobortis ege quisque<br>interdum nec tellus</p></div>
<div class="abs chef-info" style="left:845px"><h3 class="chef-name">FUSCE SUSCIPIT</h3><p class="chef-role">Malesuada Quisque</p><p class="chef-bio">Ementum ligula lobortis ege quisque<br>interdum nec tellus</p></div>

<section class="abs offer" role="img" aria-label="Dark background photo of a cook at a wood-fired oven"></section>
<h2 class="abs section-title offer-title">Our Special Offer</h2>
<p class="abs section-sub offer-sub">Praesent Rutrum Pretium Urna</p>
<div class="abs flourish on-dark offer-flourish" role="img" aria-label="Decorative scroll flourish"></div>

<h3 class="abs form-heading">RESERVATIONS FORM</h3>

<div class="abs field left row1">Full Name
  <svg width="14" height="15" viewBox="0 0 14 15"><circle cx="7" cy="4" r="3.5" fill="#fff"/><path d="M1 15v-3a4 4 0 0 1 4-4h4a4 4 0 0 1 4 4v3z" fill="#fff"/></svg></div>
<div class="abs field right row1">Your Email id
  <svg width="16" height="13" viewBox="0 0 16 13"><rect x="0" y="0" width="16" height="13" rx="1.5" fill="#fff"/><path d="M0.5 1.5L8 7l7.5-5.5" stroke="#222" stroke-width="1.4" fill="none"/></svg></div>
<div class="abs field left row2">Enter Your Phone Number
  <svg width="15" height="15" viewBox="0 0 24 24"><path d="M6.6 10.8a15.1 15.1 0 0 0 6.6 6.6l2.2-2.2a1 1 0 0 1 1-.25 11.4 11.4 0 0 0 3.6.57 1 1 0 0 1 1 1V20a1 1 0 0 1-1 1A17 17 0 0 1 3 4a1 1 0 0 1 1-1h3.5a1 1 0 0 1 1 1c0 1.25.2 2.45.57 3.57a1 1 0 0 1-.25 1z" fill="#fff"/></svg></div>
<div class="abs field right row2">1
  <span class="select-btn"><svg width="9" height="6" viewBox="0 0 9 6" style="position:static"><path d="M1 1l3.5 3.5L8 1" stroke="#fff" stroke-width="1.4" fill="none"/></svg></span></div>
<div class="abs field left row3">Pick a Date
  <svg width="15" height="15" viewBox="0 0 15 15"><rect x="0.7" y="1.7" width="13.6" height="12.6" fill="none" stroke="#fff" stroke-width="1.2"/><rect x="0.7" y="1.7" width="13.6" height="3" fill="#fff"/><g fill="#fff"><rect x="3" y="7" width="2" height="2"/><rect x="6.5" y="7" width="2" height="2"/><rect x="10" y="7" width="2" height="2"/><rect x="3" y="10.5" width="2" height="2"/><rect x="6.5" y="10.5" width="2" height="2"/><rect x="10" y="10.5" width="2" height="2"/></g></svg></div>
<div class="abs field right row3">Pick a Time
  <svg width="15" height="15" viewBox="0 0 16 16"><circle cx="8" cy="8" r="7" fill="none" stroke="#fff" stroke-width="1.4"/><path d="M8 4v4.3l2.8 1.7" stroke="#fff" stroke-width="1.4" fill="none"/></svg></div>

<p class="abs offer-note">Phasellus erat augue porta sed elit cras tincidunt elit mattis</p>
<div class="abs reserve-btn">MAKE RESERVATIONS</div>

<h2 class="abs section-title blog-title">Our Blog</h2>
<p class="abs section-sub blog-sub">Lisis Pretium Nunc</p>
<div class="abs flourish on-light blog-flourish" role="img" aria-label="Decorative scroll flourish"></div>

</body>
</html>
```